BOLD & MINIMALIST DESIGN NEEDED

We want a very bold but minimalistic business card design that is impactful and utilizes both sides of the business card. Our current logo is included for your use.

We want bold fonts and good use of negative space. We don't want the logo to overpower the design.

Target Market(s)

Professionals who are building new commercial buildings.

Industry/Entity Type

Construction

Contact Information for Business Card

Name, Title, email, office phone, cell phone, website

Font styles to use
Serif
Sans Serif

Requirements
Must have
• Bold design!

```html
<!DOCTYPE html>
<html lang="en">
<head>
<meta charset="utf-8">
<title>Summitline Design + Build — Business Card</title>
<link rel="stylesheet" href="https://fonts.googleapis.com/css2?family=Oswald:wght@600&family=Montserrat:wght@400;500&display=swap">
<style>
  :root {
    --page-bg: #d9d6d0;
    --card-bg: #ecebe7;
    --card-edge: #f8f8f6;
    --band: #262626;
    --ink: #141414;
    --lime: #8cc63f;
    --muted: #b9b9b4;
    --contact: #d6d6d2;
  }
  * { box-sizing: border-box; margin: 0; padding: 0; }
  html, body { width: 1200px; height: 887px; overflow: hidden; }
  body {
    background: var(--page-bg);
    position: relative;
    font-family: "Montserrat", sans-serif;
  }
  .business-card {
    position: absolute;
    left: 100px;
    top: 168px;
    width: 1000px;
    height: 550px;
    background: var(--card-bg);
    border: 2px solid var(--card-edge);
    border-radius: 22px;
    overflow: hidden;
    box-shadow: 0 10px 30px rgba(0,0,0,0.12);
  }
  .brand-name {
    position: absolute;
    right: 48px;
    top: 70px;
    text-align: center;
    font-family: "Oswald", sans-serif;
    font-weight: 600;
    color: var(--ink);
    line-height: 1;
  }
  .brand-name .brand-main {
    display: block;
    font-size: 56px;
    letter-spacing: 1px;
  }
  .brand-name .brand-sub {
    display: block;
    margin-top: 6px;
    font-size: 21px;
    letter-spacing: 7px;
  }
  .contact-band {
    position: absolute;
    left: 0;
    top: 255px;
    width: 780px;
    height: 268px;
    background: var(--band);
    padding: 22px 0 0 50px;
  }
  .person-name {
    font-family: "Oswald", sans-serif;
    font-weight: 600;
    font-size: 46px;
    line-height: 1;
    color: var(--lime);
    letter-spacing: 1px;
  }
  .person-title {
    margin-top: 10px;
    font-size: 20px;
    letter-spacing: 1.5px;
    color: var(--muted);
  }
  .contact-list {
    list-style: none;
    margin-top: 30px;
  }
  .contact-list li {
    display: flex;
    align-items: center;
    gap: 10px;
    height: 30px;
    font-size: 22px;
    color: var(--contact);
  }
  .contact-list svg { width: 20px; height: 20px; flex: none; }
  .contact-list .accent { color: var(--lime); }
</style>
</head>
<body>
  <div class="business-card">
    <div class="brand-name" aria-label="Summitline Design + Build">
      <span class="brand-main">SUMMITLINE</span>
      <span class="brand-sub">DESIGN + BUILD</span>
    </div>

    <section class="contact-band">
      <h1 class="person-name">DANIEL MERCER</h1>
      <p class="person-title">OWNER</p>
      <ul class="contact-list">
        <li>
          <svg viewBox="0 0 24 24" aria-hidden="true"><path fill="#8cc63f" d="M6.6 10.8a15.2 15.2 0 0 0 6.6 6.6l2.2-2.2c.3-.3.7-.4 1-.2 1.1.4 2.3.6 3.6.6.6 0 1 .4 1 1V20c0 .6-.4 1-1 1A17 17 0 0 1 3 4c0-.6.4-1 1-1h3.5c.6 0 1 .4 1 1 0 1.3.2 2.5.6 3.6.1.3 0 .7-.2 1z"/></svg>
          (555) 014-2270
        </li>
        <li>
          <svg viewBox="0 0 24 24" aria-hidden="true"><path fill="#8cc63f" d="M2 8c0-2 4.5-4 10-4s10 2 10 4v2h-5V8.5c-1.5-.5-3.2-.7-5-.7s-3.5.2-5 .7V10H2zM7 11l2-3h6l2 3 3 3v5H4v-5zm5 1.5a2.5 2.5 0 1 0 0 5 2.5 2.5 0 0 0 0-5z"/></svg>
          (555) 014-2270
        </li>
        <li>
          <svg viewBox="0 0 24 24" aria-hidden="true"><rect x="2" y="5" width="20" height="14" rx="1.5" fill="none" stroke="#8cc63f" stroke-width="2"/><path d="M3 6l9 7 9-7" fill="none" stroke="#8cc63f" stroke-width="2"/></svg>
          summitlinebuild@mail.com
        </li>
        <li>
          <svg viewBox="0 0 24 24" aria-hidden="true"><g fill="none" stroke="#8cc63f" stroke-width="1.8"><circle cx="12" cy="12" r="9.5"/><ellipse cx="12" cy="12" rx="4" ry="9.5"/><path d="M2.5 12h19M4 7h16M4 17h16"/></g></svg>
          <span>www.<span class="accent">summitline</span>build.com</span>
        </li>
      </ul>
    </section>
  </div>
</body>
</html>
```